home accents e-commerce website

I'd like a professional simple website designed where I can sell my home goods. I already have my domain name registered. I need the website to accept credit card payments and Monvex. It should have a shopping cart option and calculate sales tax and shipping costs on merchandise automatically.

I'll be taking photographs of the merchandise and writing product descriptions myself. (I'm not a professional photographer, so these photos probably won't look too polished. If you can help me make them look better, that'd be great). As I add new merchandise in the future, I'd like an option where I can log in to the back end myself and add pictures/product descriptions. And take old products down as they sell out. So the website needs to be user-friendly for me, even though I'm completely web design illiterate!

I'd like a creative, talented person who can create a whimsical, cute website. Nothing too corporate-looking.

Thank you!

Target Market(s)

women, online shoppers, New York City-area, (ship products to the United States only)

Industry/Entity Type

Home And Garden

Coding

Coded - Design and coding required

Number of Pages Required

1 page

Font styles to use
Sans Serif

Colors
0355a3
ffffff

Requirements
Must have
• shopping cart feature
• safe, secure credit card and Monvex payments
• ability for me to go in and add new products and take down old/sold products
Nice to have
• whimsical, cute design
Should not have
• too corporate-looking

```html
<!DOCTYPE html>
<html lang="en">
<head>
<meta charset="utf-8">
<title>Tovira Home Goods</title>
<link href="https://fonts.googleapis.com/css2?family=Nunito+Sans:wght@400;600;700;800&display=swap" rel="stylesheet">
<style>
:root{
  --brand:#0355a3;
  --white:#ffffff;
  --ink:#2b2b2b;
  --muted:#777777;
  --topbar:#333333;
  --line:#e2e2e2;
  --card:#f4f4f4;
  --star:#7a6b5a;
}
*{box-sizing:border-box;margin:0;padding:0}
html,body{width:1200px;height:2500px;overflow:hidden;background:var(--white)}
body{font-family:"Nunito Sans",Arial,sans-serif;color:var(--ink);position:relative}
a{color:inherit;text-decoration:none}
.wrap{position:absolute;left:97px;width:1006px}

/* top bar */
.topbar{position:absolute;top:0;left:0;width:1200px;height:28px;background:var(--topbar);color:var(--white);font-size:12px;font-weight:600}
.topbar .contact{position:absolute;left:97px;top:6px;display:flex;gap:10px}
.topbar .account{position:absolute;right:97px;top:6px;display:flex;gap:10px}
.topbar .sep{opacity:.7}

/* header */
.header{position:absolute;top:28px;left:0;width:1200px;height:99px;border-bottom:1px solid var(--line)}
.logo{position:absolute;left:97px;top:18px;color:var(--brand)}
.logo .name{font-size:44px;font-weight:800;line-height:44px;letter-spacing:1px}
.logo .sub{font-size:14px;font-weight:600;letter-spacing:4px}
.search{position:absolute;left:443px;top:30px;width:372px;height:42px;border:1px solid #cccccc;font-size:12px;color:#999;padding:13px 14px}
.search svg{position:absolute;right:12px;top:12px}
.socials{position:absolute;left:845px;top:32px;display:flex;gap:10px}
.social{width:38px;height:38px;border-radius:50%;background:var(--brand);color:var(--white);font-size:15px;font-weight:700;display:flex;align-items:center;justify-content:center}
.cart{position:absolute;left:1062px;top:30px}

/* nav */
.nav{position:absolute;top:127px;left:0;width:1200px;height:45px}
.categories{position:absolute;left:97px;top:0;width:288px;height:45px;background:var(--brand);color:var(--white);font-size:17px;font-weight:700;display:flex;align-items:center;gap:18px;padding-left:40px}
.menu{position:absolute;right:97px;top:14px;display:flex;gap:42px;font-size:15px;font-weight:600}
.menu .active{color:var(--brand)}

/* hero */
.hero{position:absolute;top:173px;left:0;width:1200px;height:485px;background:linear-gradient(180deg,#e9e8e4 0%,#dcdad5 45%,#cfd6d4 62%,#e8d27a 78%,#d6cfc4 100%)}
.hero .scene{position:absolute;left:0;top:245px;width:1200px;height:240px;background:linear-gradient(90deg,#e6de6a 0%,#2f9aa5 14%,#e06a6a 30%,#f2efd8 44%,#6ccbd8 52%,#f3d14c 64%,#e06a6a 72%,#2f9aa5 86%,#e6de6a 100%);opacity:.85}
.hero h1{position:absolute;top:70px;width:100%;text-align:center;font-size:50px;font-weight:700;letter-spacing:1px;color:#2a2a2a}
.hero p{position:absolute;top:138px;width:100%;text-align:center;font-size:20px;color:#444}
.btn{display:inline-block;border:1px solid #999;border-radius:4px;color:var(--brand);font-weight:700;text-transform:uppercase;text-align:center;background:rgba(255,255,255,.35)}
.hero .btn{position:absolute;left:523px;top:185px;width:155px;height:48px;line-height:46px;font-size:16px}
.hero .arrow{position:absolute;top:222px;width:36px;height:42px;background:rgba(120,120,120,.6);display:flex;align-items:center;justify-content:center}
.hero .arrow.left{left:0}.hero .arrow.right{right:0}

/* products */
.section-title{position:absolute;top:735px;width:1200px;text-align:center;font-size:31px;font-weight:700;letter-spacing:.5px}
.grid{position:absolute;left:97px;width:1006px;display:grid;grid-template-columns:repeat(4,230px);column-gap:28px}
.grid.row1{top:843px}.grid.row2{top:1288px}
.product .photo{width:230px;height:247px;background:var(--card);position:relative}
.product h3{margin-top:30px;font-size:17px;font-weight:600;letter-spacing:.3px}
.product .desc{margin-top:12px;font-size:12px;line-height:20px;color:var(--muted)}
.product .meta{margin-top:16px;display:flex;justify-content:space-between;align-items:center}
.product .price{font-size:16px;font-weight:700;color:var(--brand)}
.product .stars{font-size:12px;color:var(--star);letter-spacing:1px;margin-right:36px}
.photo.hovered{background:#4479b8;display:flex;flex-direction:column;align-items:center;justify-content:center;gap:14px}
.photo.hovered span{width:44px;height:44px;border:1px solid rgba(255,255,255,.8);border-radius:50%;display:flex;align-items:center;justify-content:center}
.more{position:absolute;left:495px;top:1744px;width:210px;height:48px;line-height:46px;font-size:14px;background:var(--white);border-color:#aaa}

/* promos */
.promo{position:absolute;top:1890px;height:217px;overflow:hidden}
.promo .pic{position:absolute;inset:0}
.promo .copy{position:absolute;text-align:left}
.promo h4{font-size:34px;font-weight:800;color:#222;line-height:38px}
.promo .line{font-size:22px;font-weight:600;color:#222}
.promo .btn{margin-top:18px;width:120px;height:34px;line-height:32px;font-size:14px}

/* footer */
.footer-col{position:absolute;top:2197px}
.footer-col h5{font-size:18px;font-weight:700;margin-bottom:20px}
.footer-col li{list-style:none;font-size:12px;color:#555;line-height:27.5px}
.divider{position:absolute;top:2180px;width:1px;height:210px;background:var(--line)}
.subscribe p{font-size:12px;color:#555;margin-bottom:18px}
.subscribe .field{display:flex}
.subscribe .field span{width:230px;height:36px;border:1px solid #ccc;font-size:12px;color:#777;padding:10px 12px}
.subscribe .field b{width:93px;height:36px;background:var(--brand);color:var(--white);font-size:13px;font-weight:700;line-height:36px;text-align:center}
.subscribe h6{margin-top:16px;font-size:18px;font-weight:600}
.icons{display:flex;gap:8px;margin-top:10px}
.icons span{width:34px;height:34px;border-radius:50%;background:var(--brand);color:var(--white);font-size:13px;font-weight:700;display:flex;align-items:center;justify-content:center}
.bottom-rule{position:absolute;top:2425px;left:97px;width:1006px;height:1px;background:var(--line)}
.copyright{position:absolute;top:2455px;left:97px;font-size:12px;color:#555}
.payments{position:absolute;top:2444px;right:97px;display:flex;gap:6px;align-items:center}
.payments span{height:32px;padding:0 8px;border:1px solid #bbb;border-radius:3px;font-size:12px;font-weight:700;color:var(--brand);line-height:30px}
</style>
</head>
<body>

<div class="topbar">
  <div class="contact">
    <span>&#9742; 1 555 010 0199</span><span class="sep">|</span><span>&#9993; hello@tovira.shop</span>
  </div>
  <div class="account">
    <span>&#8646; Compare</span><span class="sep">|</span><span>My Account</span><span class="sep">|</span><span>Login</span><span class="sep">|</span><span>Join</span>
  </div>
</div>

<header class="header">
  <div class="logo"><div class="name">tovira</div><div class="sub">HOME GOODS</div></div>
  <div class="search">Search Products
    <svg width="16" height="16" viewBox="0 0 16 16"><circle cx="6.5" cy="6.5" r="5" fill="none" stroke="#777" stroke-width="2"/><line x1="10.5" y1="10.5" x2="15" y2="15" stroke="#777" stroke-width="2"/></svg>
  </div>
  <div class="socials" aria-label="Social links">
    <span class="social" title="Lumo">L</span>
    <span class="social" title="Nexo">N</span>
    <span class="social" title="Kivo">K</span>
    <span class="social" title="Roza">R</span>
  </div>
  <div class="cart">
    <svg width="36" height="34" viewBox="0 0 36 34"><path d="M2 4h6l5 18h17l4-13H11" fill="none" stroke="#0355a3" stroke-width="3" stroke-linejoin="round"/><circle cx="15" cy="29" r="3" fill="#0355a3"/><circle cx="28" cy="29" r="3" fill="#0355a3"/></svg>
  </div>
</header>

<nav class="nav">
  <div class="categories">
    <svg width="16" height="14" viewBox="0 0 16 14"><rect y="0" width="16" height="2.5" fill="#fff"/><rect y="5.5" width="16" height="2.5" fill="#fff"/><rect y="11" width="16" height="2.5" fill="#fff"/></svg>
    CATEGORIES
  </div>
  <div class="menu">
    <a class="active">HOME</a><a>ABOUT TOVIRA</a><a>HOW DOES THIS CRAZINESS WORK?</a><a>CONTACT</a>
  </div>
</nav>

<section class="hero">
  <div class="scene" role="img" aria-label="Row of colourful patterned cushions on a white wooden bench"></div>
  <h1>TOVIRA HOME GOODS</h1>
  <p>At vero eos et accusamus et iusto odio dignis</p>
  <a class="btn">Shop now!</a>
  <span class="arrow left"><svg width="12" height="18" viewBox="0 0 12 18"><path d="M10 2 3 9l7 7" fill="none" stroke="#fff" stroke-width="2.5"/></svg></span>
  <span class="arrow right"><svg width="12" height="18" viewBox="0 0 12 18"><path d="M2 2l7 7-7 7" fill="none" stroke="#fff" stroke-width="2.5"/></svg></span>
</section>

<h2 class="section-title">OUR PRODUCTS</h2>

<div class="grid row1">
  <div class="product">
    <div class="photo" role="img" aria-label="Folded checked blankets" style="background:linear-gradient(135deg,#f4f4f4 20%,#5a8fcf 50%,#8fb06a 70%,#f4f4f4 90%)"></div>
    <h3>FINIBUS BONO RUM</h3>
    <p class="desc">At vero eos et accusamus et iusto odio dignissimos duci anditii</p>
    <div class="meta"><span class="price">$234.00</span><span class="stars">&#9733;&#9733;&#9733;&#9733;&#9734;</span></div>
  </div>
  <div class="product">
    <div class="photo hovered" role="img" aria-label="Glass vase with green branches, quick action overlay">
      <span><svg width="16" height="16" viewBox="0 0 16 16"><circle cx="6.5" cy="6.5" r="4.5" fill="none" stroke="#fff" stroke-width="2"/><line x1="10" y1="10" x2="14" y2="14" stroke="#fff" stroke-width="2"/></svg></span>
      <span><svg width="16" height="14" viewBox="0 0 16 14"><path d="M8 13 1.5 6.5A3.5 3.5 0 0 1 8 2a3.5 3.5 0 0 1 6.5 4.5z" fill="#fff"/></svg></span>
      <span><svg width="16" height="15" viewBox="0 0 16 15"><path d="M1 2h3l2 7h7l2-5H5" fill="none" stroke="#fff" stroke-width="1.8"/><circle cx="7" cy="13" r="1.5" fill="#fff"/><circle cx="12" cy="13" r="1.5" fill="#fff"/></svg></span>
    </div>
    <h3>FINIBUS BONO RUM</h3>
    <p class="desc">At vero eos et accusamus et iusto odio dignissimos duci anditii</p>
    <div class="meta"><span class="price">$234.00</span><span class="stars">&#9733;&#9733;&#9733;&#9733;&#9734;</span></div>
  </div>
  <div class="product">
    <div class="photo" role="img" aria-label="Stack of orange, red and green cushions" style="background:radial-gradient(circle at 50% 45%,#e2452f 0%,#f29a5a 30%,#b8c46a 45%,#f4f4f4 65%)"></div>
    <h3>FINIBUS BONO RUM</h3>
    <p class="desc">At vero eos et accusamus et iusto odio dignissimos duci anditii</p>
    <div class="meta"><span class="price">$234.00</span><span class="stars">&#9733;&#9733;&#9733;&#9733;&#9734;</span></div>
  </div>
  <div class="product">
    <div class="photo" role="img" aria-label="Round dark wooden pedestal side table" style="background:radial-gradient(ellipse at 50% 45%,#5a2a22 0%,#6e3a30 22%,#f4f4f4 55%)"></div>
    <h3>FINIBUS BONO RUM</h3>
    <p class="desc">At vero eos et accusamus et iusto odio dignissimos duci anditii</p>
    <div class="meta"><span class="price">$234.00</span><span class="stars">&#9733;&#9733;&#9733;&#9733;&#9734;</span></div>
  </div>
</div>

<div class="grid row2">
  <div class="product">
    <div class="photo" role="img" aria-label="Rolled woven rug" style="background:radial-gradient(ellipse at 50% 50%,#cbb595 0%,#d9c7a8 30%,#f4f4f4 60%)"></div>
    <h3>FINIBUS BONO RUM</h3>
    <p class="desc">At vero eos et accusamus et iusto odio dignissimos duci anditii</p>
    <div class="meta"><span class="price">$234.00</span><span class="stars">&#9733;&#9733;&#9733;&#9733;&#9734;</span></div>
  </div>
  <div class="product">
    <div class="photo" role="img" aria-label="Pink peonies in a glass vase" style="background:radial-gradient(circle at 50% 38%,#e57aa8 0%,#f0a9c4 25%,#9cba7a 40%,#f4f4f4 60%)"></div>
    <h3>FINIBUS BONO RUM</h3>
    <p class="desc">At vero eos et accusamus et iusto odio dignissimos duci anditii</p>
    <div class="meta"><span class="price">$234.00</span><span class="stars">&#9733;&#9733;&#9733;&#9733;&#9734;</span></div>
  </div>
  <div class="product">
    <div class="photo" role="img" aria-label="Blue and white striped towels and cushions" style="background:radial-gradient(ellipse at 50% 50%,#4aa3d8 0%,#8cc8ea 30%,#f4f4f4 60%)"></div>
    <h3>FINIBUS BONO RUM</h3>
    <p class="desc">At vero eos et accusamus et iusto odio dignissimos duci anditii</p>
    <div class="meta"><span class="price">$234.00</span><span class="stars">&#9733;&#9733;&#9733;&#9733;&#9734;</span></div>
  </div>
  <div class="product">
    <div class="photo" role="img" aria-label="Carved wooden nightstand with drawer" style="background:radial-gradient(ellipse at 50% 48%,#6b3520 0%,#8a4a2c 28%,#f4f4f4 58%)"></div>
    <h3>FINIBUS BONO RUM</h3>
    <p class="desc">At vero eos et accusamus et iusto odio dignissimos duci anditii</p>
    <div class="meta"><span class="price">$234.00</span><span class="stars">&#9733;&#9733;&#9733;&#9733;&#9734;</span></div>
  </div>
</div>

<a class="btn more">View more products</a>

<div class="promo" style="left:0;width:387px">
  <div class="pic" role="img" aria-label="Pink flowers in a white jug against a pale blue wall" style="background:linear-gradient(90deg,#e9a0a8 0%,#bfe0ea 35%,#cfe6ee 100%)"></div>
  <div class="copy" style="left:188px;top:40px">
    <h4>BIG SALE</h4><div class="line">UP TO 50% OFF</div><a class="btn">Shop now!</a>
  </div>
</div>
<div class="promo" style="left:407px;width:386px">
  <div class="pic" role="img" aria-label="Stacked white cushions on a pale wooden surface" style="background:linear-gradient(90deg,#c9c6c2 0%,#ebe9e6 40%,#f1efec 100%)"></div>
  <div class="copy" style="left:172px;top:52px;text-align:center">
    <h4 style="font-size:27px;font-style:italic;line-height:32px">NEW ARRIVALS</h4>
    <div class="line" style="font-size:14px;font-weight:400">At vero eoset accus ser</div>
    <a class="btn" style="margin-top:14px">Shop now!</a>
  </div>
</div>
<div class="promo" style="left:812px;width:388px">
  <div class="pic" role="img" aria-label="Stack of colourful folded woven blankets" style="background:linear-gradient(90deg,#8a5a6a 0%,#c77a5a 25%,#e9e7e3 50%,#efedea 100%)"></div>
  <div class="copy" style="left:198px;top:40px">
    <h4>SALE</h4><div class="line">UP TO 50% OFF</div><a class="btn">Shop now!</a>
  </div>
</div>

<div class="footer-col" style="left:100px">
  <h5>Information</h5>
  <ul><li>About Us</li><li>Careers</li><li>Privacy &amp; Security</li><li>Site Map</li><li>Terms of Use</li><li>Blog</li></ul>
</div>
<div class="divider" style="left:258px"></div>
<div class="footer-col" style="left:303px">
  <h5>Help &amp; support</h5>
  <ul><li>Recommended Reading</li><li>Submit your Story</li><li>Contact Us</li><li>Frequently Asked Questions</li><li>How to Order</li></ul>
</div>
<div class="divider" style="left:507px"></div>
<div class="footer-col" style="left:552px">
  <h5>My Account</h5>
  <ul><li>Delivery Information</li><li>My Account</li><li>Order Tracking</li><li>Reminder Service</li><li>Shipping, Returns &amp; Fees</li></ul>
</div>
<div class="divider" style="left:732px"></div>
<div class="footer-col subscribe" style="left:778px">
  <h5>Email Subscription</h5>
  <p>Register your email address to get information about us</p>
  <div class="field"><span>Email Address</span><b>SUBSCRIBE</b></div>
  <h6>Stay Connected</h6>
  <div class="icons">
    <span><svg width="16" height="16" viewBox="0 0 16 16"><path d="M7 9l2-2M5.5 8.5 3.5 10.5a2.1 2.1 0 0 0 3 3l2-2M10.5 7.5l2-2a2.1 2.1 0 0 0-3-3l-2 2" fill="none" stroke="#fff" stroke-width="1.6"/></svg></span>
    <span title="Lumo">L</span><span title="Nexo">N</span><span title="Quill">Q</span><span title="Kivo">K</span>
    <span><svg width="16" height="12" viewBox="0 0 16 12"><rect x="1" y="1" width="14" height="10" fill="none" stroke="#fff" stroke-width="1.5"/><path d="M1 1l7 6 7-6" fill="none" stroke="#fff" stroke-width="1.5"/></svg></span>
    <span title="Vela">V</span><span title="Roza">R</span>
  </div>
</div>

<div class="bottom-rule"></div>
<div class="copyright">Copyrights © 2017, Tovira. All Rights Reserved &nbsp;|&nbsp; Privacy Policy | Terms of Use | Feedback</div>
<div class="payments">
  <span>Cardora</span><span>Vexa</span><span>Amberpay</span><span>Dovera</span><span>Monvex</span>
</div>

</body>
</html>
```